Stationary Set Rebrand for Brennick

We are a Canadian Distribution and Service Company that was established in 1969. Over the past 5 decades we have expanded our business and have warehouses across Canada. We specialize in adhesive tapes, adhesives, films, safety, warehouse, shipping, janitorial and packaging supplies.

We have updated our logo design and would like a new corporate branding identity that includes a new fresh Stationary Set (Business Cards, Letterhead, Letterhead MS Word, Envelope, Presentation Folders, Email Signatures, Notepad Covers, etc.)

Target Market(s)

Industrial Business Sector

Font styles to use
Sans Serif

Colors
0054AA
0677BA
7BADD7
CADEEF
E8F1F8
0094D4
00A9DD
6FCCEA
C7EBF8
E9F6FB
00AB8E
00BBA5
67D7C9
C6EFE9
E9F9F6
EB3D1F
EC4F4E
F09395
F8D3D4
FCEDEE

Requirements
Should not have
• Colors not too light, darker colours preferred

```html
<!DOCTYPE html>
<html lang="en">
<head>
<meta charset="UTF-8">
<title>Brennick Business Card – Front and Back</title>
<link rel="stylesheet" href="https://fonts.googleapis.com/css2?family=Open+Sans:wght@400;700;800&display=swap">
<style>
  :root {
    --backdrop: #2b2b2b;
    --card: #ffffff;
    --card-dark: #1c1c1c;
    --pattern-light: #2a2a2a;
    --pattern-dark: #161616;
    --ink: #161616;
    --accent: #e0252b;
    --muted: #6b6b6b;
    --on-dark: #ffffff;
  }
  * { margin: 0; padding: 0; box-sizing: border-box; }
  html, body { width: 1200px; height: 900px; overflow: hidden; }
  body {
    background: var(--backdrop);
    font-family: "Open Sans", sans-serif;
    position: relative;
  }
  .card {
    position: absolute;
    left: 260px;
    width: 680px; height: 389px;
    overflow: hidden;
    box-shadow: 0 8px 24px rgba(0,0,0,0.45);
  }

  /* Front */
  .card--front { top: 40px; background: var(--card); }
  .bar { position: absolute; height: 10px; background: var(--accent); }
  .bar--top { left: 0; width: 220px; top: 84px; }
  .bar--bottom { left: 400px; right: 0; top: 290px; }
  .rule { position: absolute; left: 0; right: 0; height: 2px; background: var(--ink); }
  .rule--top { top: 96px; }
  .rule--bottom { top: 302px; }
  .brand {
    position: absolute;
    left: 230px; top: 19px;
    font-weight: 800;
    font-size: 84px;
    line-height: 1;
    letter-spacing: -2px;
    color: var(--ink);
    white-space: nowrap;
  }
  .brand-mark {
    position: absolute;
    left: 606px; top: 80px;
    width: 13px; height: 13px;
    border-radius: 50%;
    background: var(--accent);
  }
  .tagline {
    position: absolute;
    left: 300px; top: 104px;
    font-weight: 700;
    font-size: 15px;
    color: var(--ink);
    white-space: nowrap;
  }
  .person {
    position: absolute;
    right: 380px; top: 150px;
    text-align: right;
  }
  .person-name {
    font-weight: 700;
    font-size: 19px;
    color: var(--accent);
    letter-spacing: 0.3px;
    text-transform: uppercase;
    white-space: nowrap;
  }
  .person-title { font-size: 16px; color: var(--muted); white-space: nowrap; }
  .divider {
    position: absolute;
    left: 312px; top: 148px;
    width: 1px; height: 80px;
    background: var(--muted);
  }
  .contacts {
    position: absolute;
    left: 326px; top: 146px;
    list-style: none;
  }
  .contact {
    display: flex; align-items: center; gap: 8px;
    font-size: 17px;
    color: var(--muted);
    line-height: 26px;
    white-space: nowrap;
  }
  .contact svg { width: 15px; height: 15px; flex: none; }
  .address {
    position: absolute;
    left: 60px; top: 238px;
    font-size: 18px;
    color: var(--muted);
    white-space: nowrap;
  }

  /* Back */
  .card--back { top: 471px; background: var(--card-dark); }
  .back-pattern {
    position: absolute; inset: 0;
    background: linear-gradient(135deg, var(--pattern-light), var(--pattern-dark));
  }
  .back-brand {
    position: absolute;
    left: 300px; top: 140px;
  }
  .back-brand-name {
    font-weight: 800;
    font-size: 64px;
    line-height: 1;
    letter-spacing: -1.5px;
    color: var(--on-dark);
    white-space: nowrap;
  }
  .back-brand-mark {
    position: absolute;
    left: 284px; top: 48px;
    width: 10px; height: 10px;
    border-radius: 50%;
    background: var(--accent);
  }
  .back-tagline {
    margin-top: 6px;
    font-weight: 700;
    font-size: 13px;
    color: var(--on-dark);
    white-space: nowrap;
  }
</style>
</head>
<body>
  <section class="card card--front" aria-label="Brennick business card, front">
    <div class="bar bar--top"></div>
    <div class="rule rule--top"></div>
    <div class="brand">Brennick</div>
    <span class="brand-mark" aria-hidden="true"></span>
    <div class="tagline">Tape and Packaging Specialists</div>

    <div class="person">
      <div class="person-name">Daniel Hartley</div>
      <div class="person-title">Managing Director</div>
    </div>
    <div class="divider"></div>

    <ul class="contacts">
      <li class="contact">
        <svg viewBox="0 0 24 24" aria-hidden="true"><path fill="#e0252b" d="M6.6 10.8a15.1 15.1 0 0 0 6.6 6.6l2.2-2.2c.3-.3.7-.4 1-.2 1.1.4 2.3.6 3.6.6.6 0 1 .4 1 1V20c0 .6-.4 1-1 1A17 17 0 0 1 3 4c0-.6.4-1 1-1h3.5c.6 0 1 .4 1 1 0 1.3.2 2.5.6 3.6.1.3 0 .7-.2 1l-2.3 2.2z"/></svg>
        044-555 010 234
      </li>
      <li class="contact">
        <svg viewBox="0 0 24 24" aria-hidden="true"><rect x="2" y="5" width="20" height="14" rx="2" fill="#e0252b"/><path d="M3 6l9 7 9-7" fill="none" stroke="#fff" stroke-width="1.8"/></svg>
        info@brennicksupply.com
      </li>
      <li class="contact">
        <svg viewBox="0 0 24 24" aria-hidden="true"><circle cx="12" cy="12" r="10" fill="#e0252b"/><path d="M2 12h20M12 2c3 3 3 17 0 20M12 2c-3 3-3 17 0 20" fill="none" stroke="#fff" stroke-width="1.5"/></svg>
        www.brennicksupply.com
      </li>
    </ul>

    <div class="address">Your Address, City, State, Zip 0000</div>

    <div class="bar bar--bottom"></div>
    <div class="rule rule--bottom"></div>
  </section>

  <section class="card card--back" aria-label="Brennick business card, back">
    <div class="back-pattern" role="img" aria-label="Repeating pattern of dark grey maple leaves"></div>
    <div class="back-brand">
      <div class="back-brand-name">Brennick</div>
      <span class="back-brand-mark" aria-hidden="true"></span>
      <div class="back-tagline">Tape and Packaging Specialists</div>
    </div>
  </section>
</body>
</html>
```